Surya Namaskar/Sun salutation theme based 12 months desk calendar for 2016 for an indian company

1. We are a corporate support services provider, providing services in Security Management, Fire Safety Management, facility management & HR Services based out of India. pls check website: www.brelvanta.co.in
2. Need a complete 12 months desk calendar design layout for 2016 including introductory page & end page,which can then be given for printing straightaway. The calendar should be so designed that when we open any month on the front side, the back side should also give out just the same month dates layout with space to note down any important work on a date etc..All important indian festivals, gazetted hoildays should be mentioned. Any information required can be provided by us
3. Since we give this calendars as part of new year gifts, our calendar has to compete for client desk space with other calendars, it must really be very sophisticated, sleek and attractive
4. Company logo, company contact details, website details and company works must be included in the calendar but in subtle, unobtrusive way. Few details like company logo etc, can be there on all pages.Am uploading some details, rest can be taken from the website, or can be provided
5. Calendar size should be aprx 17 cm * 17 cm including the space needed for spiral. Format should be CDR Ver13 or PDF
6. Theme: Surya Namaskar poses/Sun Salutation poses. These are twelve yoga poses, prescribed for mind /body rejuvenation. Poses 1-12 should be on months Jan16 to Dec 16. A very brief writeup on the same including the relevant mantras may also be included on the page
7. Any query , please mail to rohan.mehtra@brelvanta.co.in

Target Market(s)

corporate middle & senior management MNC clients

Industry/Entity Type

Security

Requirements
Must have
• 1.company logos/contact & website details/company works with related photographs.
• 2. surya namaskar poses with a very small brief/health benefit on poses/related mantras
• 3. Indian gazetted holidays & festivals earmarked
• 4. recommendation on the printing paper type & quality/colour of cardboard base & spiral binding
• 5. Attractive Top Introduction page & end page
Nice to have
• 1. photos of the company works
• 2. End page may be used for giving company details in details
• 3. Company logo on each page
• 4. The calendar goes to a variety of corporate clients including hotels, hospitals, shopping malls, manufacturing sector, clubs etc..just for info
• 5. Related photos/same model in all months
• 6. Beautiful Female models in poses
• 7. target audience : 95% male; majority age group: 35-55; middle & senior management
• However, very receptive to any new ideas. The designer has full liberty from our side. The final parameter is that the calendar should be so attractive that it can defeat any other desk calendar competition and win that one spot on the desk
• Any queries/details required, pls mail to rohan.mehtra@brelvanta.co.in
Should not have
• Religious overtones

```html
<!DOCTYPE html>
<html lang="en">
<head>
<meta charset="utf-8">
<title>Brelvanta 2016 Desk Calendar – March</title>
<link rel="stylesheet" href="https://fonts.googleapis.com/css2?family=Montserrat:wght@600;700&family=Gelasio:ital,wght@1,500;1,700&display=swap">
<style>
  :root {
    --cream: #f7e8cb;
    --green: #2b6b5e;
    --orange: #f5a11f;
    --yellow: #f3d42c;
    --holiday: #f2a623;
    --white: #ffffff;
  }
  html, body {
    margin: 0;
    padding: 0;
    width: 1200px;
    height: 1200px;
    overflow: hidden;
    background: var(--cream);
  }
  .page {
    position: absolute;
    left: 0;
    top: 0;
    width: 1156px;
    height: 1156px;
    background: var(--cream);
    transform: scale(1.03806);
    transform-origin: 0 0;
    overflow: hidden;
  }
  .decor {
    position: absolute;
    left: 0;
    top: 0;
    width: 1156px;
    height: 1156px;
  }
  .month-title {
    position: absolute;
    left: 540px;
    width: 584px;
    top: 62px;
    margin: 0;
    text-align: center;
    font-family: "Montserrat", sans-serif;
    font-weight: 700;
    font-size: 46px;
    letter-spacing: 1px;
    color: var(--green);
  }
  .weekdays {
    position: absolute;
    left: 540px;
    top: 122px;
    width: 584px;
    display: grid;
    grid-template-columns: repeat(7, 1fr);
    font-family: "Montserrat", sans-serif;
    font-weight: 600;
    font-size: 17px;
    color: var(--green);
    text-align: center;
  }
  .date-grid {
    position: absolute;
    left: 540px;
    top: 153px;
    width: 584px;
    height: 417px;
    display: grid;
    grid-template-columns: repeat(7, 1fr);
    grid-template-rows: repeat(5, 1fr);
    border-top: 2px solid var(--green);
    border-left: 2px solid var(--green);
    box-sizing: border-box;
  }
  .day {
    border-right: 2px solid var(--green);
    border-bottom: 2px solid var(--green);
    font-family: "Montserrat", sans-serif;
    font-weight: 600;
    font-size: 24px;
    color: var(--green);
    text-align: right;
    padding: 0 5px 0 0;
    line-height: 28px;
  }
  .day.holiday { color: var(--holiday); }
  .pose-title {
    position: absolute;
    left: 530px;
    top: 626px;
    margin: 0;
    font-family: "Gelasio", serif;
    font-style: italic;
    font-weight: 700;
    font-size: 39px;
    line-height: 56px;
    color: var(--green);
  }
  .pose-meaning {
    position: absolute;
    left: 524px;
    top: 792px;
    margin: 0;
    font-family: "Gelasio", serif;
    font-style: italic;
    font-weight: 500;
    font-size: 33px;
    line-height: 46px;
    color: var(--green);
  }
  .holiday-list {
    position: absolute;
    left: 44px;
    top: 1006px;
    margin: 0;
    padding: 0;
    list-style: none;
    font-family: "Gelasio", serif;
    font-style: italic;
    font-weight: 500;
    font-size: 33px;
    line-height: 47px;
    color: var(--green);
  }
  .holiday-list li::before { content: "• "; }
  .holiday-list sup { font-size: 18px; }
  .brand {
    position: absolute;
    left: 1020px;
    top: 1060px;
    width: 130px;
    text-align: left;
    color: var(--white);
    font-family: "Montserrat", sans-serif;
  }
  .brand-mark {
    display: block;
    width: 26px;
    height: 26px;
    background: var(--white);
    margin: 0 0 8px 36px;
  }
  .brand-name {
    font-weight: 700;
    font-size: 15px;
    letter-spacing: 0.5px;
  }
  .brand-tagline {
    font-weight: 600;
    font-size: 7px;
    line-height: 9px;
  }
</style>
</head>
<body>
<div class="page">
  <svg class="decor" viewBox="0 0 1156 1156" xmlns="http://www.w3.org/2000/svg">
    <defs>
      <linearGradient id="photoTone" x1="0" y1="0" x2="1" y2="1">
        <stop offset="0" stop-color="#e4e4e2"/>
        <stop offset="0.5" stop-color="#f1f1ef"/>
        <stop offset="1" stop-color="#d9d8d6"/>
      </linearGradient>
      <linearGradient id="sunBand" x1="0" y1="0" x2="1" y2="0">
        <stop offset="0" stop-color="#f39a1f"/>
        <stop offset="0.5" stop-color="#f5c826"/>
        <stop offset="1" stop-color="#f59c1e"/>
      </linearGradient>
      <linearGradient id="sunPill" x1="0" y1="0" x2="1" y2="0">
        <stop offset="0" stop-color="#f39a1f"/>
        <stop offset="0.45" stop-color="#f3d42c"/>
        <stop offset="1" stop-color="#f5a11f"/>
      </linearGradient>
    </defs>
    <path class="photo" role="img" aria-label="Photograph: woman in black top and grey trousers performing the Hasta Padasana standing forward bend on a white mat"
          d="M0,0 L440,0 L440,560 C440,640 420,660 360,662 C250,665 120,640 0,618 Z" fill="url(#photoTone)"/>
    <path class="sun-band" d="M0,742 L0,806 C160,800 330,780 470,752 L470,735 Z" fill="url(#sunBand)"/>
    <path class="mantra-pill" d="M430,606 L837,606 A75,75 0 0 1 837,756 L430,756 Z" fill="url(#sunPill)"/>
    <path class="green-frame"
          d="M432,0 L505,0 L505,580 C505,720 470,775 380,776 C250,776 110,760 0,745 L0,618 C120,640 250,665 360,662 C420,660 440,640 440,560 L440,0 Z"
          fill="var(--green)"/>
    <circle class="brand-corner" cx="1156" cy="1156" r="196" fill="var(--green)"/>
  </svg>

  <h1 class="month-title">MARCH</h1>
  <div class="weekdays">
    <span>SUN</span><span>MON</span><span>TUE</span><span>WED</span><span>THU</span><span>FRI</span><span>SAT</span>
  </div>
  <div class="date-grid">
    <div class="day"></div><div class="day"></div><div class="day">1</div><div class="day">2</div><div class="day">3</div><div class="day">4</div><div class="day">5</div>
    <div class="day">6</div><div class="day">7</div><div class="day">8</div><div class="day">9</div><div class="day">10</div><div class="day">11</div><div class="day">12</div>
    <div class="day">13</div><div class="day">14</div><div class="day">15</div><div class="day">16</div><div class="day">17</div><div class="day">18</div><div class="day">19</div>
    <div class="day">20</div><div class="day">21</div><div class="day">22</div><div class="day">23</div><div class="day holiday">24</div><div class="day holiday">25</div><div class="day">26</div>
    <div class="day">27</div><div class="day">28</div><div class="day">29</div><div class="day">30</div><div class="day">31</div><div class="day"></div><div class="day"></div>
  </div>

  <h2 class="pose-title">3. Om Hroom<br>Suryaya Namah</h2>
  <p class="pose-meaning">Prostration to Him<br>who induces activity.</p>

  <ul class="holiday-list">
    <li>Holi - 24<sup>th</sup> March 2016</li>
    <li>Good Friday - 25<sup>th</sup> March 2016</li>
  </ul>

  <div class="brand">
    <span class="brand-mark"></span>
    <div class="brand-name">BRELVANTA</div>
    <div class="brand-tagline">Your one stop business companion<br>ISO 9001:2008 Certified</div>
  </div>
</div>
</body>
</html>
```